Bus Wrap (Advertisement for Realtor)

NOTE: Please check zip file, there are 3 .rar files there, all the references needed for the information below are all in the zip file. Thank you!

It is a design to wrap a shuttle bus, (please see attached file for instructions)

1. Please see pictures in folder BUS, this bus will be wrapped in this design, show it on it how it will look
2. In folder IDEA you will see realistic ideas of wraps, let’s see if we can accomplish something like this
3. In the folder IDEA you will see a picture named SAMPLE, something like this is simple and catching but try to implement this simplicity with a realistic 3D design that will stand out.
4. In folder TEXT you will find all the needs it text
5. In a folder PICTURES you will find a picture of a person we going to use on this bus. Depending on your idea and design this person will be photographed as need it for your idea. We will make a photo of this lady on solid green or blue background in a requested position that you can replace as need it per your design or you will tell us where to take a picture of this lady based on your idea. Also, she has been photographed in a bright purple blouse, we prefer to stay with this color of her blouse, but if your idea is perfect and calling for a different outfit please let us know so we can make this request and take her picture as you describing.
6. In folder LOGO you can use a logo that will fit your color palette of the design. Do not make this logo big, it must be there by law but we do not advertise them so make it small or in someplace that is not important.
7. Bus will be wrapped full with windows, but you will still see frames of the windows because they are not flat with a surface of the buss, so in your design please make sure that it does not go on the middle of the face for example.
8. Cabin of the bus can be painted in any solid color to match your design, or the design can overlap the cabin
9. Wheels can be painted in any color
10. Bumpers can be painted in any color

Target Market(s)

People who looking to buy, sell or lease the house

Industry/Entity Type

real estate

Font styles to use
Other font styles liked:
• easy to read from a long distance, for example 5 cars away

Colors
6B429C
8869AF
B7A5CE
E3DAEB
F3F0F8

Requirements
Must have
• good realistic design, see examples
Nice to have
• 3D is nice to have
Should not have
• clipart

```html
<!DOCTYPE html>
<html lang="en">
<head>
<meta charset="utf-8">
<title>Realtor Shuttle Bus Rear Wrap</title>
<link rel="stylesheet" href="https://fonts.googleapis.com/css2?family=Montserrat:wght@400;500;600;700;800&display=swap">
<style>
  :root{
    --page:#ffffff;
    --wrap-grey:#5f5f61;
    --wrap-grey-dark:#545456;
    --stripe-red:#d0232a;
    --stripe-white:#ffffff;
    --text-white:#ffffff;
    --accent-red:#d0232a;
    --accent-purple:#8869af;
    --deep-purple:#6b429c;
  }
  html,body{margin:0;padding:0;overflow:hidden;background:var(--page);}
  .canvas{
    position:relative;width:1200px;height:1000px;overflow:hidden;
    background:var(--page);font-family:"Montserrat",sans-serif;
  }
  .wrap-panel{position:absolute;left:230px;top:150px;width:740px;height:700px;}
  .wrap-shape{position:absolute;inset:0;}
  .wrap-content{
    position:absolute;left:0;right:0;top:120px;
    display:flex;flex-direction:column;align-items:center;
    color:var(--text-white);text-align:center;
  }
  .agent-name{
    margin:0;font-size:42px;font-weight:800;letter-spacing:1px;
    text-shadow:2px 0 var(--accent-red),-2px 0 var(--accent-red),0 2px var(--accent-red),0 -2px var(--accent-red),
                2px 2px var(--accent-red),-2px -2px var(--accent-red),2px -2px var(--accent-red),-2px 2px var(--accent-red);
  }
  .phone-row{display:flex;align-items:center;gap:14px;margin-top:14px;}
  .phone-icon{width:70px;height:70px;}
  .phone-number{
    font-size:72px;font-weight:800;line-height:1;
    text-shadow:3px 0 var(--deep-purple),-3px 0 var(--deep-purple),0 3px var(--deep-purple),0 -3px var(--deep-purple),
                3px 3px var(--deep-purple),-3px -3px var(--deep-purple),3px -3px var(--deep-purple),-3px 3px var(--deep-purple);
  }
  .call-note{font-size:38px;font-weight:700;margin-top:10px;}
  .email{font-size:25px;font-weight:500;margin-top:4px;}
  .tagline{font-size:32px;font-weight:500;margin-top:14px;color:var(--accent-purple);letter-spacing:.5px;}
  .tagline .strong{color:var(--accent-red);font-weight:800;}
  .services{display:flex;align-items:center;gap:18px;margin-top:44px;font-size:40px;font-weight:800;letter-spacing:1px;}
  .services .divider{width:4px;height:62px;background:var(--accent-red);}
  .brokerage{display:flex;align-items:center;gap:14px;margin-top:64px;font-size:34px;font-weight:700;letter-spacing:2px;}
  .brokerage .mark{width:36px;height:36px;border:4px solid var(--text-white);box-sizing:border-box;}
</style>
</head>
<body>
<div class="canvas">
  <div class="wrap-panel">
    <svg class="wrap-shape" viewBox="0 0 740 700" width="740" height="700" aria-hidden="true">
      <path d="M20 70 Q20 20 80 14 Q370 -6 660 14 Q720 20 720 70 L720 690 Q720 700 710 700 L30 700 Q20 700 20 690 Z" fill="var(--wrap-grey)"/>
      <path d="M20 62 Q22 20 80 14 Q370 -6 660 14 Q718 20 720 62 Q560 30 370 48 Q180 68 20 62 Z" fill="var(--stripe-white)"/>
      <path d="M40 34 Q80 16 130 13 Q370 -4 640 13 Q700 18 712 40 Q560 22 370 42 Q190 60 40 34 Z" fill="var(--stripe-red)"/>
      <rect x="20" y="640" width="700" height="60" fill="var(--wrap-grey-dark)" opacity=".35"/>
    </svg>
    <div class="wrap-content">
      <h1 class="agent-name">MARINA DELACOURT</h1>
      <div class="phone-row">
        <svg class="phone-icon" viewBox="0 0 70 70" aria-hidden="true">
          <circle cx="35" cy="35" r="31" fill="var(--text-white)" stroke="var(--accent-purple)" stroke-width="5"/>
          <path d="M22 20 Q18 24 20 31 Q25 44 39 50 Q46 52 50 48 L46 41 Q44 39 41 41 L38 43 Q30 39 27 32 L29 29 Q31 26 29 24 Z" fill="var(--wrap-grey)"/>
        </svg>
        <span class="phone-number">555-014-2736</span>
      </div>
      <div class="call-note">call or text</div>
      <div class="email">marina@brightkeyhomes.net</div>
      <div class="tagline">YOUR <span class="strong">REALTOR</span> FOR <span class="strong">LIFE</span></div>
      <div class="services">
        <span>BUY</span><span class="divider"></span><span>SELL</span><span class="divider"></span><span>LEASE</span>
      </div>
      <div class="brokerage"><span class="mark"></span><span>HARBOR REALTY</span></div>
    </div>
  </div>
</div>
</body>
</html>
```